holloway paving service

Needs to have phone number 0418259730 and email markholloway@brightmail.com.au.
ABN 62318470915
name mark holloway

For all your concreting solutions
Excavation
Exposed & colour concrete
House & shed slabs
Driveways
Landing & steps

Contact Information for Business Card

ph 0418259730
email markholloway@brightmail.com.au.
ABN 62318470915
name mark holloway

```html
<!DOCTYPE html>
<html lang="en">
<head>
<meta charset="utf-8">
<title>Holloway Paving Service – Business Card</title>
<link href="https://fonts.googleapis.com/css2?family=Roboto:wght@400;500;700&family=Roboto+Condensed:wght@700&display=swap" rel="stylesheet">
<style>
  :root {
    --backdrop: #2a2a2a;
    --card-white: #f3f3f3;
    --brand-orange: #f26a22;
    --ink-grey: #4a4a4a;
    --white: #ffffff;
  }
  * { margin: 0; padding: 0; box-sizing: border-box; }
  html, body {
    width: 1200px;
    height: 960px;
    overflow: hidden;
    background: var(--backdrop);
    font-family: "Roboto", Arial, sans-serif;
  }
  .canvas { position: relative; width: 1200px; height: 960px; }

  .card {
    position: absolute;
    width: 600px;
    height: 342px;
    box-shadow: 0 3px 6px rgba(0,0,0,0.45);
  }
  .card--front { left: 321px; top: 110px; background: var(--card-white); }
  .card--back  { left: 320px; top: 493px; background: var(--brand-orange); }

  /* front: brand lockup */
  .brand-lockup {
    position: absolute;
    left: 52px;
    top: 146px;
    display: flex;
    align-items: center;
    gap: 12px;
  }
  .brand-lockup__mark {
    width: 44px;
    height: 44px;
    background: var(--brand-orange);
  }
  .brand-lockup__name {
    font-weight: 700;
    font-size: 15px;
    line-height: 18px;
    color: var(--brand-orange);
    text-transform: uppercase;
    letter-spacing: 0.2px;
  }

  /* front: contact block */
  .contact {
    position: absolute;
    left: 328px;
    top: 98px;
    color: var(--ink-grey);
    font-size: 14px;
  }
  .contact__name {
    font-family: "Roboto Condensed", "Roboto", sans-serif;
    font-weight: 700;
    font-size: 23px;
    color: var(--brand-orange);
    text-transform: uppercase;
    margin-bottom: 9px;
  }
  .contact__list { list-style: none; }
  .contact__item {
    display: flex;
    align-items: center;
    gap: 8px;
    height: 19px;
  }
  .contact__icon { width: 13px; height: 13px; fill: var(--brand-orange); flex: none; }
  .contact__abn { margin-top: 11px; }

  /* back */
  .back-brand {
    position: absolute;
    left: 0; right: 0;
    top: 120px;
    display: flex;
    justify-content: center;
    align-items: center;
    gap: 14px;
    color: var(--white);
    font-weight: 700;
    font-size: 26px;
    text-transform: uppercase;
  }
  .back-brand__mark { width: 40px; height: 40px; background: var(--white); }
  .services {
    position: absolute;
    left: 0; right: 0;
    top: 271px;
    text-align: center;
    color: var(--white);
    font-size: 14.5px;
    line-height: 18px;
  }
  .services__sep { font-size: 9px; vertical-align: 2px; margin: 0 4px; }
</style>
</head>
<body>
<main class="canvas">

  <section class="card card--front" aria-label="Business card front">
    <div class="brand-lockup">
      <span class="brand-lockup__mark"></span>
      <span class="brand-lockup__name">Holloway Paving Service</span>
    </div>

    <div class="contact">
      <h1 class="contact__name">Mark Holloway</h1>
      <ul class="contact__list">
        <li class="contact__item">
          <svg class="contact__icon" viewBox="0 0 24 24" aria-hidden="true"><path d="M6.6 10.8a15.1 15.1 0 0 0 6.6 6.6l2.2-2.2c.3-.3.7-.4 1-.2 1.1.4 2.3.6 3.6.6.6 0 1 .4 1 1V20c0 .6-.4 1-1 1A17 17 0 0 1 3 4c0-.6.4-1 1-1h3.5c.6 0 1 .4 1 1 0 1.3.2 2.5.6 3.6.1.3 0 .7-.2 1z"/></svg>
          <span>0418259730</span>
        </li>
        <li class="contact__item">
          <svg class="contact__icon" viewBox="0 0 24 24" aria-hidden="true"><path d="M2 5h20v14H2z M2 5l10 7 10-7" fill="var(--brand-orange)"/><path d="M3 6l9 6.3L21 6" fill="none" stroke="#f3f3f3" stroke-width="1.6"/></svg>
          <span>markholloway@brightmail.com.au</span>
        </li>
        <li class="contact__item">
          <svg class="contact__icon" viewBox="0 0 24 24" aria-hidden="true"><circle cx="12" cy="12" r="10"/><path d="M2 12h20M12 2c3 3 3 17 0 20M12 2c-3 3-3 17 0 20" fill="none" stroke="#f3f3f3" stroke-width="1.5"/></svg>
          <span>www.hollowaypaving.com.au</span>
        </li>
      </ul>
      <p class="contact__abn">ABN 62318470915</p>
    </div>
  </section>

  <section class="card card--back" aria-label="Business card back">
    <div class="back-brand">
      <span class="back-brand__mark"></span>
      <span>Holloway Paving Service</span>
    </div>
    <p class="services">
      Excavation <span class="services__sep">◆</span> Exposed &amp; colour concrete<br>
      House &amp; shed slabs <span class="services__sep">◆</span> Driveways <span class="services__sep">◆</span> Landing &amp; steps
    </p>
  </section>

</main>
</body>
</html>
```